Trevani.com- International Goal Achievement Coach Needs Website Design

I need a web design for my new company called Trevani. I help people who are stuck, people who have a big dream, but don't know how to get there. I help them to break their dreams down into small, manageable steps... and then I'm the "kick in the shin" to get them moving and thriving!

We can all be better- We can all DO better. I inspire people to Go Boldly in the direction of your dreams.

I have uploaded my logo along with some vintage champagne posters. Please use the vintage posters as inspiration. I like the bold, vintage look and feel. I would love the main colors of the design to be black, white and metallic gold. And to follow along this vintage look and feel. Please feel free to use the logo in black or metallic gold or white.

Target Market(s)

websites that I like- lunabrask.com & tessak.tv

I would like to also use the vintage champagne photos attached as inspiration as well.

Industry/Entity Type

It Company

Requirements
Must have
• Tabs should include: About, Work With Me, Praise, Giving Back

On the homepage add:
* Sign up for newsletter with space to enter name and email (No click throughs)
* Upcoming Events/Sessions
* Newsletter Posts
* Resources
* Praise Section

* Large photo on top with additional photos throughout the page/site.
Nice to have
• Any additions you can bring to the table would be greatly appreciated.

```html
<!DOCTYPE html>
<html lang="en">
<head>
<meta charset="utf-8">
<title>Trevani — Goal Achievement Coach</title>
<link href="https://fonts.googleapis.com/css2?family=Kumbh+Sans:wght@400;600;700&family=Pinyon+Script&family=Arimo:ital,wght@0,400;0,700;1,400&display=swap" rel="stylesheet">
<style>
:root{
  --gold:#b8862a;
  --gold-dark:#9c6f1f;
  --ink:#1a1a1a;
  --text:#3a3a3a;
  --canvas:#e8e8e8;
  --band:#e2e2e2;
  --white:#ffffff;
  --rule:#dedede;
  --plum:#8e3f5c;
  --cream:#f2eee5;
  --social:#9c6a3c;
}
*{box-sizing:border-box;margin:0;padding:0}
html,body{width:1200px;height:1000px;overflow:hidden;background:var(--canvas)}
body{position:relative;font-family:"Arimo",Arial,sans-serif;color:var(--text)}
.abs{position:absolute}
.page{left:248px;top:0;width:704px;height:1000px;background:var(--white)}
.topbar{left:248px;top:0;width:704px;height:33px;background:var(--gold)}
.nav{top:13px;font:700 6.5px "Kumbh Sans",sans-serif;color:var(--white);letter-spacing:.2px}
.lang{left:894px;top:13px;font:400 5.5px "Kumbh Sans",sans-serif;color:var(--white)}
.brand{left:381px;top:0;width:93px;height:49px;background:var(--white);border-radius:0 0 5px 5px;display:flex;align-items:center;justify-content:center;gap:6px;box-shadow:0 1px 3px rgba(0,0,0,.2)}
.brand-dot{width:24px;height:24px;border-radius:50%;background:var(--gold)}
.brand-name{font:600 12px "Kumbh Sans",sans-serif;color:var(--gold)}
.hero{left:248px;top:33px;width:704px;height:238px;background:radial-gradient(ellipse at 62% 35%,#f0c48a 0%,#d99a4e 22%,transparent 45%),linear-gradient(90deg,#5a3412 0%,#a86a2a 30%,#c98a3e 55%,#e8c9a0 78%,#b7855a 100%)}
.hero-title{left:380px;top:104px;width:200px;text-align:center;font:700 27px/28px "Kumbh Sans",sans-serif;color:var(--white);letter-spacing:-.5px}
.hero-script{left:380px;top:156px;width:200px;text-align:center;font:400 32px "Pinyon Script",cursive;color:var(--white)}
.signup{left:248px;top:271px;width:704px;height:42px;background:var(--band)}
.signup-title{left:387px;top:278px;font:700 12.5px "Kumbh Sans",sans-serif;color:var(--ink)}
.signup-title span{font:400 16px "Pinyon Script",cursive}
.signup-sub{left:387px;top:295px;font:400 6.5px "Kumbh Sans",sans-serif;color:var(--gold)}
.signup-sub b{font-weight:700}
.field{top:285px;width:111px;height:13px;background:var(--white);border:1px solid #cfcfcf;border-radius:2px;font:400 5.5px Arial,sans-serif;color:#777;padding:3px 5px}
.start{left:764px;top:276px;width:33px;height:33px;border-radius:50%;background:var(--gold);color:var(--white);text-align:center;font:700 7px/7px "Kumbh Sans",sans-serif;padding-top:9px;box-shadow:0 0 0 2px #d9d9d9}
.start i{font:400 9px "Pinyon Script",cursive;display:block;margin-top:1px}
.post-title{font:600 13px "Kumbh Sans",sans-serif;color:var(--ink)}
.post-title.sm{font-size:8.5px}
.tag{height:10px;padding:0 12px 0 6px;background:var(--gold);color:var(--white);font:700 5px/10px "Kumbh Sans",sans-serif;clip-path:polygon(0 0,100% 0,88% 50%,100% 100%,0 100%)}
.photo{border-radius:4px}
.copy{font:400 6px/9.5px Arial,sans-serif;color:var(--text)}
.copy a{color:var(--gold);text-decoration:none}
.subhead{font:700 7.5px Arial,sans-serif;color:var(--ink)}
.label{font:700 6px "Kumbh Sans",sans-serif;color:var(--gold)}
.share{top:673px;height:13px;border:1px solid var(--gold);border-radius:2px;font:400 5.5px/11px Arial,sans-serif;color:var(--text);padding:0 4px;display:flex;align-items:center;gap:3px}
.share b{background:#555;color:var(--white);border-radius:4px;font-size:4px;padding:0 2px;line-height:6px}
.rule{height:1px;background:var(--rule)}
.more{font:700 5.5px "Kumbh Sans",sans-serif;color:var(--gold)}
.social{top:335px;width:15px;height:15px;border-radius:50%;background:var(--social)}
.side-head{font:700 7.5px "Kumbh Sans",sans-serif;color:var(--ink)}
.events{left:685px;top:386px;width:121px;height:111px;border-radius:22px 0 22px 0;overflow:hidden;background:linear-gradient(120deg,#b8d4df 0%,#f1d6c0 45%,#e7b38f 75%,#d99f7b 100%)}
.events-panel{left:685px;top:410px;width:70px;height:87px;background:var(--plum);color:var(--white);padding:7px 5px 0}
.events-panel h4{font:700 5px "Kumbh Sans",sans-serif}
.events-panel p{font:400 4.5px "Kumbh Sans",sans-serif;opacity:.85}
.ev{border-top:1px solid rgba(255,255,255,.3);margin-top:5px;padding-top:5px;position:relative}
.ev::after{content:"›";position:absolute;right:0;top:5px;font-size:9px;line-height:8px}
.popular{left:685px;top:533px;width:121px;list-style:none}
.popular li{font:400 5.8px/8.5px Arial,sans-serif;color:var(--gold);padding-left:9px;margin-bottom:4.6px;position:relative}
.popular li::before{content:"›";position:absolute;left:0;top:0;color:#999}
.resource{left:685px;width:121px;height:45px;border-radius:3px;background:linear-gradient(90deg,#2a2a2a 0%,#3d3d3d 55%,#8a8a8a 80%,#bdbdbd 100%);color:var(--white);padding:7px 6px}
.resource .big{font:700 6.5px/7px "Kumbh Sans",sans-serif}
.resource .scr{font:italic 400 6.5px/7px Georgia,serif}
.resource .huge{font:700 12px/12px "Kumbh Sans",sans-serif;margin-top:6px}
.resource .small{font:400 5.5px "Kumbh Sans",sans-serif}
.praise{left:686px;top:792px;width:117px;height:114px;background:var(--cream);border:1px solid #e3dccb;border-radius:3px}
.praise-mark{left:692px;top:796px;font:700 24px Georgia,serif;color:#c9c1ae}
.praise-text{left:714px;top:801px;width:80px;font:italic 400 5.5px/8.2px Arial,sans-serif;color:#555}
.praise-who{left:717px;top:882px;font:italic 700 5.5px Arial,sans-serif;color:var(--ink)}
.older{left:381px;top:937px;font:700 6px "Kumbh Sans",sans-serif;color:var(--gold)}
.footer{left:248px;top:975px;width:704px;height:25px;background:#000;color:var(--white);text-align:center;font:400 5.5px/25px Arial,sans-serif}
</style>
</head>
<body>
<div class="abs page"></div>

<header>
  <div class="abs topbar"></div>
  <div class="abs brand"><span class="brand-dot"></span><span class="brand-name">Trevani</span></div>
  <nav>
    <span class="abs nav" style="left:645px">ABOUT</span>
    <span class="abs nav" style="left:685px">WORK WITH ME</span>
    <span class="abs nav" style="left:745px">PRAISE</span>
    <span class="abs nav" style="left:786px">GIVING BACK</span>
  </nav>
  <span class="abs lang">Select language ▾</span>
</header>

<section>
  <div class="abs hero" role="img" aria-label="Large photo of a smiling woman with long hair in warm autumn sunlight"></div>
  <h1 class="abs hero-title">I help people who have a big</h1>
  <div class="abs hero-script">Dream</div>
</section>

<section>
  <div class="abs signup"></div>
  <div class="abs signup-title">Achieve your <span>Goals</span></div>
  <div class="abs signup-sub">Sign up for weekly updates. <b>It's FREE</b></div>
  <div class="abs field" style="left:521px">Name</div>
  <div class="abs field" style="left:640px">Email</div>
  <div class="abs start">START<i>now!</i></div>
</section>

<main>
  <h2 class="abs post-title" style="left:381px;top:334px">The Secret to Success</h2>
  <div class="abs tag" style="left:381px;top:356px">8 comments</div>
  <div class="abs photo" style="left:381px;top:376px;width:259px;height:111px;background:linear-gradient(180deg,#e9eef0 0%,#b7c98a 45%,#7e9a3a 75%,#d9c84a 100%)" role="img" aria-label="Photo of a girl in a sunny meadow holding a flowing white scarf"></div>
  <p class="abs copy" style="left:381px;top:495px;width:262px">Sed ut perspiciatis unde omnis iste natus error sit voluptatem accusantium doloremque laudantium, totam rem aperiam, eaque ipsa quae ab illo inventore veritatis et quasi architecto beatae vitae dicta sunt explicabo.</p>
  <p class="abs copy" style="left:381px;top:534px;width:262px">Neque porro quisquam est, qui dolorem ipsum quia dolor sit amet, consectetur, adipisci velit, sed quia non numquam eius modi tempora incidunt ut <a>labore et dolore magnam aliquam</a> quaerat voluptatem.</p>
  <h3 class="abs subhead" style="left:381px;top:563px">The 3 most common self-help questions:</h3>
  <p class="abs copy" style="left:381px;top:582px;width:262px">Lorem ipsum dolor sit amet, consectetur adipisicing elit, sed do eiusmod tempor incididunt ut labore et dolore magna aliqua.</p>
  <p class="abs copy" style="left:381px;top:611px;width:262px">Sed ut perspiciatis unde omnis iste natus error sit voluptatem accusantium doloremque laudantium, totam rem aperiam, eaque ipsa quae ab illo inventore veritatis et quasi architecto beatae vitae dicta sunt explicabo.</p>
  <div class="abs label" style="left:381px;top:655px">Sharing is Caring</div>
  <div class="abs share" style="left:381px">Friendly <b>1.2k</b></div>
  <div class="abs share" style="left:436px">Chirper <b>2.4k</b></div>
  <div class="abs share" style="left:483px">Pinboard <b>800</b></div>
  <div class="abs share" style="left:537px">Linkup <b>300</b></div>
  <div class="abs rule" style="left:381px;top:708px;width:259px"></div>

  <h2 class="abs post-title sm" style="left:381px;top:729px">How to Feel More Fulfilled</h2>
  <div class="abs tag" style="left:381px;top:750px">8 comments</div>
  <div class="abs photo" style="left:381px;top:769px;width:111px;height:81px;background:linear-gradient(135deg,#f3e58a 0%,#d7dc8c 40%,#9fd0a9 75%,#6fbf9c 100%)" role="img" aria-label="Photo of a woman leaping joyfully in bright sunlight"></div>
  <p class="abs copy" style="left:381px;top:857px;width:115px">Lorem ipsum dolor sit amet, consectetur adipisicing elit, sed do eiusmod tempor incididunt ut labore et dolore magna aliqua.</p>
  <div class="abs more" style="left:381px;top:891px">Read More</div>

  <h2 class="abs post-title sm" style="left:529px;top:729px">How to handle success</h2>
  <div class="abs tag" style="left:529px;top:750px">8 comments</div>
  <div class="abs photo" style="left:529px;top:769px;width:111px;height:81px;background:linear-gradient(135deg,#f4f4f4 0%,#e2e2e2 45%,#3b4660 70%,#d9d4cc 100%)" role="img" aria-label="Photo of a smiling woman at a desk in a bright office"></div>
  <p class="abs copy" style="left:529px;top:857px;width:115px">Lorem ipsum dolor sit amet, consectetur adipisicing elit, sed do eiusmod tempor incididunt ut labore et dolore magna aliqua.</p>
  <div class="abs more" style="left:529px;top:891px">Read More</div>

  <div class="abs rule" style="left:381px;top:919px;width:259px"></div>
  <div class="abs older">⟵ OLDER POSTS</div>
</main>

<aside>
  <span class="abs social" style="left:704px"></span>
  <span class="abs social" style="left:727px"></span>
  <span class="abs social" style="left:749px"></span>
  <span class="abs social" style="left:771px"></span>

  <h3 class="abs side-head" style="left:685px;top:367px">Upcoming Events and Sessions</h3>
  <div class="abs events" role="img" aria-label="Photo of a woman with long hair outdoors in soft light"></div>
  <div class="abs events-panel">
    <h4>WE CAN ALL BE BETTER</h4>
    <p>we can all do better</p>
    <div class="ev"><h4>EVENT #1</h4><p>December 20</p></div>
    <div class="ev"><h4>EVENT #2</h4><p>December 28</p></div>
    <div class="ev" style="border-top:0"><p style="font-weight:700">VIEW ALL</p></div>
  </div>

  <h3 class="abs side-head" style="left:685px;top:510px">Most Popular</h3>
  <div class="abs rule" style="left:685px;top:523px;width:121px"></div>
  <ul class="abs popular">
    <li>How To Change The World &amp; Live Your Purpose w/ Owen Hartley</li>
    <li>The Mental Exercise That Can Turn Wishes Into Reality</li>
    <li>Who Else Influences Your Customers</li>
    <li>Value What You Do: A Must Watch For Artists and Creatives</li>
    <li>Why Smart People Underperform &amp; What To Do About It</li>
  </ul>

  <h3 class="abs side-head" style="left:685px;top:642px">Resources</h3>
  <div class="abs resource" style="top:658px" role="img" aria-label="Banner with a black and white photo of a smiling woman">
    <div class="big">I INSPIRE PEOPLE<br>TO GO BOLDLY</div>
    <div class="scr">in the direction<br>of your dreams.</div>
  </div>
  <div class="abs resource" style="top:711px" role="img" aria-label="Banner with a black and white photo of a smiling woman">
    <div class="huge">OVERCOME</div>
    <div class="small">FEAR AND SELF DOUBT</div>
  </div>

  <h3 class="abs side-head" style="left:685px;top:773px">Praise</h3>
  <div class="abs rule" style="left:685px;top:786px;width:121px"></div>
  <div class="abs praise"></div>
  <div class="abs praise-mark">“</div>
  <p class="abs praise-text">I would like to thank you for helping me to first visualise, and then to accurately define my business goals. Your business coaching has crystallised, and then confirmed the main reasons for my own personal goals, and my business goals.</p>
  <div class="abs praise-who">– Mara Quill</div>
</aside>

<footer class="abs footer">© 2010 Trevani.</footer>
</body>
</html>
```